Updated DJ business Card showing other businesses

DJ Talbo offers professional mobile dj services including DJ. MC. Karaoke.
Silent Disco (will attach logo)
I also offer a 360 Photo Booth.

Contact info:
(405) 555-0147
mark.fenstell@pelimail.com
Social Media @DJTalboOKC

```html
<!DOCTYPE html>
<html lang="en">
<head>
<meta charset="utf-8">
<title>DJ Talbo – Business Card</title>
<link rel="stylesheet" href="https://fonts.googleapis.com/css2?family=Lato:wght@400;700;900&family=Saira+Condensed:ital,wght@0,700;0,800;1,800&display=swap">
<style>
  :root {
    --stage: #2b2b2d;
    --card-black: #0b0b0c;
    --card-white: #ffffff;
    --brand-red: #d81f4a;
    --ink: #111111;
    --ink-soft: #333333;
    --white: #ffffff;
    --faint: #efefef;
    --badge: #3a3a3d;
  }
  * { margin: 0; padding: 0; box-sizing: border-box; }
  html, body { width: 1200px; height: 900px; overflow: hidden; }
  body { background: var(--stage); position: relative; font-family: "Lato", sans-serif; }

  .card {
    position: absolute;
    width: 630px;
    height: 360px;
    border-radius: 24px;
    overflow: hidden;
    box-shadow: 0 14px 30px rgba(0,0,0,0.45);
  }

  /* Front side */
  .card--front { left: 500px; top: 50px; background: var(--card-black); }
  .partner-badge {
    position: absolute; left: 34px; top: 28px;
    width: 96px; height: 38px; border-radius: 19px;
    background: var(--badge);
  }
  .front-wordmark {
    position: absolute; left: 0; right: 0; top: 96px;
    text-align: center;
    font-family: "Saira Condensed", sans-serif;
    font-weight: 800; font-size: 112px; line-height: 1;
    letter-spacing: 2px;
    color: var(--brand-red);
  }
  .front-tagline {
    position: absolute; left: 0; right: 0; top: 214px;
    text-align: center;
    font-family: "Saira Condensed", sans-serif;
    font-style: italic; font-weight: 800; font-size: 27px;
    letter-spacing: 0.5px;
    color: var(--brand-red);
  }
  .front-services {
    position: absolute; left: 0; right: 0; top: 262px;
    text-align: center;
    font-family: "Saira Condensed", sans-serif;
    font-weight: 700; font-size: 25px; letter-spacing: 1px;
    color: var(--white);
  }
  .front-extra {
    position: absolute; left: 0; right: 0; top: 296px;
    text-align: center;
    font-family: "Saira Condensed", sans-serif;
    font-style: italic; font-weight: 700; font-size: 15px; letter-spacing: 1.5px;
    color: var(--white);
  }

  /* Back side */
  .card--back { left: 70px; top: 470px; background: var(--card-white); }
  .back-decoration {
    position: absolute; left: 40px; top: 20px;
    width: 240px; height: 320px; border-radius: 50%;
    background: var(--faint);
  }
  .back-wordmark {
    position: absolute; right: 40px; top: 44px;
    font-family: "Lato", sans-serif; font-weight: 900; font-size: 46px;
    letter-spacing: 1px; color: var(--brand-red);
  }
  .holder { position: absolute; left: 44px; top: 118px; }
  .holder-name {
    font-weight: 900; font-size: 38px; letter-spacing: 0.5px; color: var(--ink);
  }
  .holder-title {
    margin-top: 2px; font-weight: 400; font-size: 17px; color: var(--brand-red);
  }
  .divider {
    position: absolute; left: 44px; right: 40px; top: 200px;
    height: 1px; background: var(--ink-soft);
  }
  .contacts { position: absolute; left: 44px; top: 216px; list-style: none; }
  .contact {
    display: flex; align-items: center; gap: 10px;
    font-size: 16px; color: var(--ink-soft); margin-bottom: 8px;
  }
  .contact--phone { font-weight: 700; font-size: 22px; color: var(--ink); }
  .contact-icon { width: 16px; height: 16px; flex: none; }
  .social {
    position: absolute; right: 40px; bottom: 30px;
    font-size: 18px; font-weight: 700; color: var(--ink-soft);
  }
</style>
</head>
<body>

  <section class="card card--front" aria-label="Business card front">
    <div class="partner-badge" aria-hidden="true"></div>
    <div class="front-wordmark">DJ TALBO</div>
    <p class="front-tagline">OFFERS PROFESSIONAL MOBILE DJ SERVICES</p>
    <p class="front-services">DJ | MC | KARAOKE | SILENT DISCO</p>
    <p class="front-extra">I ALSO OFFER A 360 PHOTO BOOTH.</p>
  </section>

  <section class="card card--back" aria-label="Business card back">
    <div class="back-decoration" aria-hidden="true"></div>
    <div class="back-wordmark">DJ TALBO</div>

    <div class="holder">
      <h1 class="holder-name">DJ TALBO</h1>
      <p class="holder-title">Founder/Owner/DJ/Trumpet Player/Vocalist</p>
    </div>

    <div class="divider"></div>

    <ul class="contacts">
      <li class="contact contact--phone">
        <svg class="contact-icon" viewBox="0 0 24 24" aria-hidden="true"><path fill="#d81f4a" d="M6.6 10.8a15 15 0 0 0 6.6 6.6l2.2-2.2a1 1 0 0 1 1-.25 11.4 11.4 0 0 0 3.6.57 1 1 0 0 1 1 1V20a1 1 0 0 1-1 1A17 17 0 0 1 3 4a1 1 0 0 1 1-1h3.5a1 1 0 0 1 1 1c0 1.25.2 2.45.57 3.57a1 1 0 0 1-.25 1z"/></svg>
        (405) 555-0147
      </li>
      <li class="contact">
        <svg class="contact-icon" viewBox="0 0 24 24" aria-hidden="true"><rect x="2" y="5" width="20" height="14" rx="1" fill="#d81f4a"/><path d="M2 6l10 7 10-7" stroke="#fff" stroke-width="1.8" fill="none"/></svg>
        mark.fenstell@pelimail.com
      </li>
      <li class="contact">
        <svg class="contact-icon" viewBox="0 0 24 24" aria-hidden="true"><circle cx="12" cy="12" r="10" fill="none" stroke="#d81f4a" stroke-width="2.2"/><path d="M2 12h20M12 2c3 3 3 17 0 20M12 2c-3 3-3 17 0 20" stroke="#d81f4a" stroke-width="1.6" fill="none"/></svg>
        www.dj-talbo.com
      </li>
    </ul>

    <p class="social">@DJTalboOKC</p>
  </section>

</body>
</html>
```